Full re-design of visual identity

We have just re-designed our logo and would like to apply it on our folders, business cards, stationery, and etc... we are attaching new logo + the material we need to re-design... we will provide full corel draw files to help make job easier and also because lot of icons and artwork can be still used...

any doubts we are at your disposal. thanks in advance.

```html
<!DOCTYPE html>
<html lang="en">
<head>
<meta charset="utf-8">
<title>Orbilink Stationery Identity</title>
<link href="https://fonts.googleapis.com/css2?family=Roboto:wght@400;700&family=Tinos&display=swap" rel="stylesheet">
<style>
  :root{
    --canvas:#f2f2f2;
    --paper:#fbfbfb;
    --paper-edge:#e4e4e4;
    --orange:#e0620e;
    --orange-deep:#c9520a;
    --orange-soft:#f2b083;
    --ink:#222;
    --brand-gray:#6c6c6c;
    --muted:#8a8a8a;
    --faint:#e6e6e6;
  }
  *{box-sizing:border-box;margin:0;padding:0}
  html,body{width:1200px;height:795px;overflow:hidden;background:var(--canvas)}
  body{position:relative;font-family:"Roboto",Arial,sans-serif}
  .sheet{position:absolute;background:var(--paper);box-shadow:0 1px 3px rgba(0,0,0,.12);overflow:hidden}
  .sheet svg.bg{position:absolute;inset:0;width:100%;height:100%}
  .brand{position:absolute;display:flex;align-items:center;gap:4px}
  .brand-name{font-family:"Roboto",Arial,sans-serif;font-weight:700;color:var(--brand-gray);letter-spacing:-.5px;line-height:1}
  .brand-dot{border-radius:50%;background:var(--orange)}
  .slogan{position:absolute;font-family:"Roboto",Arial,sans-serif;font-weight:400;color:var(--muted);white-space:nowrap;letter-spacing:.3px}
  .deco-circle{position:absolute;border-radius:50%;background:var(--faint)}

  /* letterhead */
  .letterhead{left:298px;top:38px;width:274px;height:370px}
  .letter{position:absolute;left:40px;top:84px;width:200px;font-family:"Tinos","Times New Roman",serif;font-size:6.1px;line-height:7.3px;color:var(--ink)}
  .letter p{text-align:justify;margin-bottom:7px}
  .letter .salute{margin-bottom:10px}
  .closing{position:absolute;left:40px;top:231px;font-family:"Tinos","Times New Roman",serif;font-size:6.1px;line-height:7.3px;color:var(--ink)}
  .signature{position:absolute;left:40px;top:248px;width:46px;height:15px;background:#e9e9e9}
  .signer{position:absolute;left:40px;top:263px;font-family:"Tinos","Times New Roman",serif;font-size:6.1px;color:var(--ink)}
  .contact{position:absolute;left:34px;top:330px;font-size:4.3px;line-height:6px;color:#777}
  .contact li{list-style:none;display:flex;align-items:center;gap:5px}
  .contact li::before{content:"";width:3px;height:3px;background:var(--orange);border-radius:50%}

  /* folder */
  .folder{left:597px;top:38px;width:314px;height:383px}

  /* cards */
  .card{height:65px;width:118px}
  .card-front{left:296px;top:436px}
  .card-back{left:453px;top:436px}
  .card-person{position:absolute;right:10px;top:28px;text-align:right;font-size:4.6px;color:#444;line-height:6px}
  .card-person .role{color:var(--orange)}
  .card-contact{position:absolute;left:12px;top:40px;font-size:3.4px;line-height:4.4px;color:#777}
  .card-contact li{list-style:none;display:flex;align-items:center;gap:3px}
  .card-contact li::before{content:"";width:2px;height:2px;background:var(--orange);border-radius:50%}

  /* envelopes */
  .envelope-back{left:612px;top:447px;width:290px;height:144px}
  .envelope-front{left:613px;top:612px;width:293px;height:150px}

  /* notebook */
  .notebook{left:289px;top:562px;width:139px;height:200px}
  .spiral{position:absolute;left:0;top:6px;width:8px;height:188px;background:repeating-linear-gradient(to bottom,#555 0 1.5px,transparent 1.5px 5px)}

  /* small goods */
  .keytag{left:467px;top:582px;width:48px;height:83px;border-radius:5px;background:#fdfdfd;border:1px solid #ddd}
  .eraser{left:474px;top:683px;width:29px;height:79px;border-radius:2px}
  .mark-only{position:absolute;left:50%;transform:translateX(-50%);border-radius:50%;background:var(--orange)}
</style>
</head>
<body>

<!-- Letterhead -->
<section class="sheet letterhead">
  <svg class="bg" viewBox="0 0 274 370" preserveAspectRatio="none" aria-hidden="true">
    <path d="M0 360 Q150 348 274 316 L274 370 L0 370Z" fill="var(--orange-soft)"/>
    <path d="M0 364 Q160 352 274 326 L274 370 L0 370Z" fill="var(--orange)"/>
  </svg>
  <div class="deco-circle" style="left:180px;top:8px;width:56px;height:56px"></div>
  <div class="brand" style="left:46px;top:24px">
    <span class="brand-name" style="font-size:21px">Orbilink</span>
    <span class="brand-dot" style="width:9px;height:9px"></span>
  </div>
  <span class="slogan" style="left:50px;top:47px;font-size:4.5px">networks · cloud · support</span>
  <div class="letter">
    <p class="salute">Gentlemen,</p>
    <p>Enclosed please find the article we discussed last month, which I would be pleased to see featured in your next issue. I have reviewed every section with care and made the changes you suggested; the closing part now reads more clearly and the figures have been checked twice. If you accept the piece, kindly send the agreed amount by the end of the month, as it would help me settle a few pending matters. Should you need further edits, I am glad to make them, and the text can be shortened to suit your pages.</p>
    <p>I hope you will read this request in the best possible light. Our last meeting left much unsaid, and I regret any confusion it may have caused. The revised version replaces the old opening and gives the article a more complete and thoughtful form. I would be very glad to meet again at some future time, under better circumstances.</p>
  </div>
  <div class="closing">In the meantime I remain<br>Yours very truly,</div>
  <div class="signature" role="img" aria-label="Handwritten signature"></div>
  <div class="signer">Elias Marrow</div>
  <ul class="contact">
    <li>(555) 014-2270</li>
    <li>(555) 014-2271</li>
    <li>hello@orbilink.net</li>
    <li>www.orbilink.net</li>
  </ul>
</section>

<!-- Presentation folder -->
<section class="sheet folder">
  <svg class="bg" viewBox="0 0 314 383" preserveAspectRatio="none" aria-hidden="true">
    <path d="M0 96 Q40 140 130 152 Q240 164 314 128 L314 383 L0 383Z" fill="var(--orange)"/>
    <path d="M0 96 Q40 140 130 152 Q240 164 314 128 L314 150 Q240 186 130 176 Q50 166 0 120Z" fill="var(--orange-deep)" opacity=".35"/>
    <path d="M170 150 Q250 150 314 128 L314 148 Q250 174 170 150Z" fill="var(--orange-soft)"/>
  </svg>
  <div class="deco-circle" style="left:212px;top:4px;width:66px;height:66px"></div>
  <div class="brand" style="left:94px;top:74px">
    <span class="brand-name" style="font-size:25px">Orbilink</span>
    <span class="brand-dot" style="width:11px;height:11px"></span>
  </div>
  <span class="slogan" style="left:98px;top:101px;font-size:5px">networks · cloud · support</span>
</section>

<!-- Business card front -->
<section class="sheet card card-front">
  <svg class="bg" viewBox="0 0 118 65" preserveAspectRatio="none" aria-hidden="true">
    <path d="M0 62 Q60 59 118 50 L118 65 L0 65Z" fill="var(--orange)"/>
  </svg>
  <div class="brand" style="left:12px;top:8px">
    <span class="brand-name" style="font-size:13px">Orbilink</span>
    <span class="brand-dot" style="width:6px;height:6px"></span>
  </div>
  <div class="card-person">Daniel Reyes<br><span class="role">President</span></div>
  <ul class="card-contact">
    <li>(555) 014-2270</li>
    <li>(555) 014-2271</li>
    <li>hello@orbilink.net</li>
    <li>www.orbilink.net</li>
  </ul>
</section>

<!-- Business card back -->
<section class="sheet card card-back">
  <div class="deco-circle" style="left:70px;top:4px;width:36px;height:36px;background:var(--orange)"></div>
  <div class="brand" style="left:12px;top:44px">
    <span class="brand-name" style="font-size:13px">Orbilink</span>
    <span class="brand-dot" style="width:6px;height:6px"></span>
  </div>
</section>

<!-- Envelope back -->
<section class="sheet envelope-back">
  <svg class="bg" viewBox="0 0 290 144" preserveAspectRatio="none" aria-hidden="true">
    <path d="M4 4 L10 48 L280 48 L286 4" fill="none" stroke="var(--paper-edge)" stroke-width="1"/>
  </svg>
  <div class="mark-only" style="top:12px;width:16px;height:16px"></div>
</section>

<!-- Notebook -->
<section class="sheet notebook">
  <div class="spiral"></div>
  <div class="brand" style="left:36px;top:88px">
    <span class="brand-name" style="font-size:16px">Orbilink</span>
    <span class="brand-dot" style="width:7px;height:7px"></span>
  </div>
  <span class="slogan" style="left:38px;top:106px;font-size:3.6px">networks · cloud · support</span>
</section>

<!-- Key tag -->
<section class="sheet keytag">
  <div class="mark-only" style="top:24px;width:12px;height:12px"></div>
  <div class="brand" style="left:9px;top:48px">
    <span class="brand-name" style="font-size:8px">Orbilink</span>
  </div>
</section>

<!-- Eraser -->
<section class="sheet eraser">
  <div class="mark-only" style="top:36px;width:10px;height:10px"></div>
</section>

<!-- Envelope front -->
<section class="sheet envelope-front">
  <div class="deco-circle" style="left:180px;top:8px;width:70px;height:70px"></div>
  <div class="brand" style="left:28px;top:20px">
    <span class="brand-name" style="font-size:21px">Orbilink</span>
    <span class="brand-dot" style="width:9px;height:9px"></span>
  </div>
  <span class="slogan" style="left:32px;top:43px;font-size:4.5px">networks · cloud · support</span>
</section>

</body>
</html>
```